Redesign a Start-Up Dating Website

Website: https://morvelique.com.
Make sure the design has an island style theme.
I would like the 7 pages of my website to have a new and professional look. I want the same colors to remain, but I want a creative look for all the pages. This is a dating website that is in the startup stage. So, I want to give my entire website a custom makeover. I want something that will stand out from the other dating sites. Something that will attract more people to want to use my services, and hopefully get new members.
Target Market(s)
Dating
Industry/Entity Type
Dating
Coding
Coded - Design and coding required
Number of Pages Required
5+ page
Font styles to use
Other font styles liked:
- Decorative, San Serif
Requirements
Must have
- The design must have the original colors and a stylish font to go along. The design must be creative, welcoming, and professional. I would like an island style theme for the website. This is a dating website so make sure that the design is tailored to that aspect.
Nice to have
- It would be nice to have a decorative font and a professional style on all the pages. Make sure the design will be mobile responsive and friendly for all the pages on the website.
Should not have
- The design should not be bland and uncreative.

```html
<!DOCTYPE html>
<html lang="en">
<head>
<meta charset="utf-8">
<title>Morvelique – Dating is Easy</title>
<link href="https://fonts.googleapis.com/css2?family=Roboto:wght@400;500;700&family=Open+Sans:wght@400;600;700&display=swap" rel="stylesheet">
<style>
  :root{
    --purple:#6b3f98;
    --teal:#35b59f;
    --orange:#f7901e;
    --logo-green:#5fa98c;
    --ink:#333333;
    --muted:#555555;
    --white:#ffffff;
    --light:#f4f6f8;
  }
  *{box-sizing:border-box;margin:0;padding:0}
  html,body{width:1200px;height:2276px;overflow:hidden}
  body{position:relative;background:var(--white);font-family:"Open Sans",Arial,sans-serif;color:var(--ink)}
  .abs{position:absolute}
  .head{font-family:"Roboto",Arial,sans-serif;font-weight:700}

  /* header */
  .site-header{left:0;top:0;width:1200px;height:102px;background:var(--white)}
  .brand{display:flex;align-items:center;gap:10px}
  .brand-dot{width:52px;height:52px;border-radius:50%;background:var(--orange)}
  .brand-name{font-family:"Roboto",Arial,sans-serif;font-weight:700;font-size:36px;color:var(--logo-green)}
  .nav-link{top:44px;font-family:"Open Sans",Arial,sans-serif;font-weight:700;font-size:13px;letter-spacing:.5px;color:#333}
  .nav-link.active{color:var(--purple)}
  .btn-register{left:969px;top:36px;width:75px;height:37px;background:var(--teal);color:#fff;font-size:12px;font-weight:700;display:flex;align-items:center;justify-content:center;border-radius:2px}
  .btn-login{left:1051px;top:36px;width:75px;height:37px;border:2px solid var(--orange);color:var(--orange);font-size:12px;font-weight:700;display:flex;align-items:center;justify-content:center;border-radius:2px}

  /* hero */
  .hero{left:0;top:102px;width:1200px;height:427px;background:linear-gradient(90deg,#eef4f9 0%,#dfeaf3 55%,#e6eef5 100%)}
  .hero-photo{left:690px;top:102px;width:510px;height:427px;background:linear-gradient(160deg,#6a4a3c 0%,#a87760 35%,#2c8fa0 70%,#1e7d8e 100%)}
  .hero-title{left:76px;top:212px;font-size:43px;color:var(--purple)}
  .hero-sub{left:76px;top:272px;font-family:"Roboto",Arial,sans-serif;font-weight:500;font-size:24px;line-height:34px;color:#333}
  .hero-cta{left:76px;top:396px;width:344px;height:38px;background:var(--teal);color:#fff;font-family:"Roboto",Arial,sans-serif;font-weight:700;font-size:15px;display:flex;align-items:center;justify-content:center;letter-spacing:.3px}

  /* quick search */
  .search-band{left:0;top:529px;width:1200px;height:258px;background:var(--purple)}
  .search-card{left:76px;top:561px;width:420px;height:196px;background:var(--orange);padding:26px 22px}
  .search-card h2{font-family:"Roboto",Arial,sans-serif;font-weight:700;font-size:31px;color:#fff;margin-bottom:18px}
  .search-card li{list-style:none;color:#fff;font-size:14.5px;font-weight:600;display:flex;align-items:center;gap:16px;margin-bottom:12px}
  .field-label{font-size:12px;font-weight:600;color:#fff;letter-spacing:.3px}
  .select{width:294px;height:38px;background:#fff;border-radius:3px;font-size:13px;color:#333;display:flex;align-items:center;justify-content:space-between;padding:0 14px}
  .btn-search{left:831px;top:719px;width:295px;height:38px;background:var(--teal);color:#fff;font-family:"Roboto",Arial,sans-serif;font-weight:700;font-size:16px;display:flex;align-items:center;justify-content:center}

  /* members */
  .community-title{left:76px;top:858px;font-size:30px;line-height:39px}
  .community-title .teal{color:var(--teal)}
  .community-title .purple{color:var(--purple)}
  .member-photo{top:836px;width:187px;height:164px}
  .member-photo.featured{outline:4px solid var(--orange);outline-offset:-4px}
  .member-name{top:1019px;width:187px;text-align:center;font-family:"Roboto",Arial,sans-serif;font-weight:700;font-size:17px;color:var(--purple)}
  .member-meta{top:1042px;width:187px;text-align:center;font-size:13.5px;color:#444}

  /* benefits */
  .benefits-photo{left:0;top:1127px;width:700px;height:345px;background:linear-gradient(120deg,#e7e2dc 0%,#d8cabd 45%,#a7b8c8 80%,#c9d2db 100%)}
  .benefits-panel{left:0;top:1127px}
  .benefits-title{left:677px;top:1196px;font-size:31px;color:#fff}
  .benefits-sub{left:677px;top:1250px;font-family:"Roboto",Arial,sans-serif;font-weight:700;font-size:25px;line-height:38px;color:#fff}
  .btn-plans{left:677px;top:1355px;width:295px;height:42px;background:var(--purple);color:#fff;font-family:"Roboto",Arial,sans-serif;font-weight:700;font-size:16px;display:flex;align-items:center;justify-content:center}

  /* steps */
  .step{top:1525px;width:300px;text-align:center}
  .step-icon{width:97px;height:97px;border-radius:50%;background:var(--orange);margin:0 auto;display:flex;align-items:center;justify-content:center}
  .step h3{font-family:"Roboto",Arial,sans-serif;font-weight:700;font-size:17px;color:var(--orange);margin-top:22px;letter-spacing:.3px}
  .step p{font-size:14.5px;line-height:24px;color:#444;margin-top:12px;padding:0 20px}

  /* subscribe */
  .subscribe{left:0;top:1839px;width:1200px;height:206px;background:var(--purple);overflow:hidden}
  .subscribe-title{left:0;top:1884px;width:1200px;text-align:center;font-size:24px;color:#fff}
  .email-input{left:343px;top:1937px;width:343px;height:43px;background:#fff;font-size:14px;color:#333;display:flex;align-items:center;padding-left:14px}
  .btn-subscribe{left:699px;top:1937px;width:158px;height:43px;background:var(--orange);color:#fff;font-family:"Roboto",Arial,sans-serif;font-weight:700;font-size:14px;display:flex;align-items:center;justify-content:center}

  /* footer */
  .footer-head{top:2085px;font-family:"Roboto",Arial,sans-serif;font-weight:700;font-size:15px;color:var(--teal);letter-spacing:.4px}
  .footer-about{left:76px;top:2111px;width:330px;font-size:13.5px;line-height:23px;color:#333}
  .read-more{left:76px;top:2210px;font-size:13.5px;font-weight:700;color:var(--purple)}
  .footer-links{list-style:none;font-size:13.5px;color:#333}
  .footer-links li{height:29px}
  .copyright{left:887px;top:2150px;font-size:12.5px;line-height:21px;color:#333}
</style>
</head>
<body>

<!-- Header -->
<header class="abs site-header">
  <div class="abs brand" style="left:76px;top:28px">
    <span class="brand-dot"></span>
    <span class="brand-name">Morvelique</span>
  </div>
  <nav>
    <a class="abs nav-link active" style="left:387px">HOME</a>
    <a class="abs nav-link" style="left:457px">SEARCH</a>
    <a class="abs nav-link" style="left:538px">MEMBERS</a>
    <a class="abs nav-link" style="left:633px">EXTRAS</a>
    <a class="abs nav-link" style="left:713px">ABOUT</a>
    <a class="abs nav-link" style="left:788px">PREMIUM</a>
    <a class="abs nav-link" style="left:882px">CONTACT</a>
  </nav>
  <a class="abs btn-register">REGISTER</a>
  <a class="abs btn-login">LOG IN</a>
</header>

<!-- Hero -->
<section class="abs hero"></section>
<div class="abs hero-photo" role="img" aria-label="Smiling couple embracing"></div>
<h1 class="abs head hero-title">Dating is EASY with Morvelique</h1>
<p class="abs hero-sub">Sign-Up For A 30 Days Free Trial<br>Enjoy All The Benefits Morvelique Has To Offer<br>With A Full Membership.</p>
<a class="abs hero-cta">START MORVELIQUING WITH FREE SIGN-UP</a>

<!-- Quick search -->
<section class="abs search-band"></section>
<div class="abs search-card">
  <h2>QUICK SEARCH</h2>
  <ul>
    <li><svg width="12" height="10" viewBox="0 0 12 10"><path d="M1 5l3.5 3.5L11 1.5" stroke="#fff" stroke-width="2.4" fill="none"/></svg>Let's Find Your Perfect Match Today</li>
    <li><svg width="12" height="10" viewBox="0 0 12 10"><path d="M1 5l3.5 3.5L11 1.5" stroke="#fff" stroke-width="2.4" fill="none"/></svg>Find Your Perfect Match For Free!</li>
    <li><svg width="12" height="10" viewBox="0 0 12 10"><path d="M1 5l3.5 3.5L11 1.5" stroke="#fff" stroke-width="2.4" fill="none"/></svg>Online Dating Made Easy On Morvelique.Com</li>
  </ul>
</div>
<span class="abs field-label" style="left:525px;top:557px">I AM:</span>
<span class="abs field-label" style="left:831px;top:557px">SEEKING A:</span>
<span class="abs field-label" style="left:525px;top:630px">AGE:</span>
<span class="abs field-label" style="left:831px;top:630px">TO:</span>
<div class="abs select" style="left:525px;top:581px">Man<svg width="8" height="12" viewBox="0 0 8 12"><path d="M0 5l4-5 4 5zM0 7l4 5 4-5z" fill="#333"/></svg></div>
<div class="abs select" style="left:831px;top:581px;width:295px">Woman<svg width="8" height="12" viewBox="0 0 8 12"><path d="M0 5l4-5 4 5zM0 7l4 5 4-5z" fill="#333"/></svg></div>
<div class="abs select" style="left:525px;top:655px">18<svg width="8" height="12" viewBox="0 0 8 12"><path d="M0 5l4-5 4 5zM0 7l4 5 4-5z" fill="#333"/></svg></div>
<div class="abs select" style="left:831px;top:655px;width:295px">99<svg width="8" height="12" viewBox="0 0 8 12"><path d="M0 5l4-5 4 5zM0 7l4 5 4-5z" fill="#333"/></svg></div>
<div class="abs select" style="left:525px;top:719px">Select Country<svg width="8" height="12" viewBox="0 0 8 12"><path d="M0 5l4-5 4 5zM0 7l4 5 4-5z" fill="#333"/></svg></div>
<a class="abs btn-search">SEARCH</a>

<!-- Community -->
<h2 class="abs head community-title"><span class="teal">JOIN THIS<br>COMMUNITY OF</span><br><span class="purple">1 MORVELIQUE<br>MEMBERS</span></h2>
<svg class="abs" style="left:74px;top:1036px" width="40" height="18" viewBox="0 0 40 18"><path d="M9 2L2 9l7 7" stroke="#333" stroke-width="2.5" fill="none"/><path d="M29 2l7 7-7 7" stroke="#333" stroke-width="2.5" fill="none"/></svg>

<div class="abs member-photo featured" style="left:343px;background:linear-gradient(135deg,#e3b9a6,#8f2b2b)" role="img" aria-label="Member profile photo"></div>
<div class="abs member-photo" style="left:542px;background:linear-gradient(135deg,#6b6b6b,#caa38a)" role="img" aria-label="Member profile photo"></div>
<div class="abs member-photo" style="left:740px;background:linear-gradient(135deg,#f1e6b8,#6b4530)" role="img" aria-label="Member profile photo"></div>
<div class="abs member-photo" style="left:939px;background:linear-gradient(135deg,#cbb79d,#2f2a3a)" role="img" aria-label="Member profile photo"></div>

<span class="abs member-name" style="left:343px">NAME HEADING</span>
<span class="abs member-name" style="left:542px">NAME HEADING</span>
<span class="abs member-name" style="left:740px">NAME HEADING</span>
<span class="abs member-name" style="left:939px">NAME HEADING</span>
<span class="abs member-meta" style="left:343px">26, United States</span>
<span class="abs member-meta" style="left:542px">26, United States</span>
<span class="abs member-meta" style="left:740px">26, United States</span>
<span class="abs member-meta" style="left:939px">26, United States</span>

<!-- Benefits -->
<div class="abs benefits-photo" role="img" aria-label="Woman smiling while using a laptop on a sofa"></div>
<svg class="abs benefits-panel" width="1200" height="345" viewBox="0 0 1200 345"><polygon points="645,0 1200,0 1200,345 555,345" fill="#35b59f"/></svg>
<h2 class="abs head benefits-title">BENEFITS</h2>
<p class="abs benefits-sub">AFFORDABLE EASY SIGN-UP AND<br>CANCELLATION PROCESSES</p>
<a class="abs btn-plans">VIEW MEMBERSHIP PLANS</a>

<!-- Steps -->
<div class="abs step" style="left:90px">
  <div class="step-icon"><svg width="40" height="40" viewBox="0 0 40 40"><rect x="3" y="5" width="30" height="32" rx="4" fill="#fff"/><path d="M14 26l2-7 13-13 5 5-13 13z" fill="#f7901e"/><path d="M16 24l1.5-4.5L30 7l3 3-12.5 12.5z" fill="#fff"/></svg></div>
  <h3>CREATE A PROFILE</h3>
  <p>Let people know all about you; the good and the quirky-show the world your true colors and find someone with the same unique qualities as you.</p>
</div>
<div class="abs step" style="left:450px">
  <div class="step-icon"><svg width="44" height="44" viewBox="0 0 44 44"><circle cx="14" cy="9" r="5" fill="#fff"/><path d="M7 16h14v14h-3v12h-8V30H7z" fill="#fff"/><circle cx="30" cy="9" r="5" fill="#fff"/><path d="M23 16h14l2 14h-4v12h-8V30h-4z" fill="#fff"/></svg></div>
  <h3>FIND MATCHES</h3>
  <p>Browse other users and feel the excitement of getting your first message and getting to know potential dates in a safe and fun environment.</p>
</div>
<div class="abs step" style="left:809px">
  <div class="step-icon"><svg width="42" height="38" viewBox="0 0 42 38"><path d="M21 36S3 24 3 12a9 9 0 0118-2 9 9 0 0118 2c0 12-18 24-18 24z" fill="#fff"/></svg></div>
  <h3>START DATING</h3>
  <p>Once you've found your potential soulmate, it's time to meet up and say 'Hello' to the start of your journey together.</p>
</div>

<!-- Subscribe -->
<section class="abs subscribe">
  <svg class="abs" style="left:200px;top:20px" width="320" height="230" viewBox="0 0 320 230"><g transform="rotate(20 160 115)" fill="none" stroke="#ffffff" stroke-opacity=".08" stroke-width="14"><rect x="30" y="30" width="260" height="170" rx="20"/><path d="M40 45l120 90 120-90"/></g></svg>
</section>
<h2 class="abs head subscribe-title">SUBSCRIBE FOR UPDATES</h2>
<div class="abs email-input">Enter Email Address</div>
<a class="abs btn-subscribe">SUBSCRIBE</a>

<!-- Footer -->
<footer>
  <h4 class="abs footer-head" style="left:76px">ABOUT</h4>
  <p class="abs footer-about">Morvelique aims to provide a straight-forward, easy-to-use online dating service. I won't over-complicate things or reduce the amount of people you can talk to with algorithms.</p>
  <a class="abs read-more">Read More</a>

  <h4 class="abs footer-head" style="left:437px">QUICK LINKS</h4>
  <ul class="abs footer-links" style="left:437px;top:2112px"><li>Morvelique</li><li>About</li><li>Contact</li><li>Login</li></ul>
  <ul class="abs footer-links" style="left:537px;top:2112px"><li>Members</li><li>Premium</li><li>Register</li><li>Search</li></ul>

  <h4 class="abs footer-head" style="left:702px">EXTRAS</h4>
  <ul class="abs footer-links" style="left:702px;top:2112px"><li>Chat</li><li>Meet Me</li><li>Date Tracker</li><li>Trending</li></ul>

  <div class="abs brand" style="left:887px;top:2090px">
    <span class="brand-dot" style="width:50px;height:50px"></span>
    <span class="brand-name" style="font-size:34px">Morvelique</span>
  </div>
  <p class="abs copyright">Copyright © &nbsp;Morvelique 2017 .<br>All rights reserved.</p>
</footer>

</body>
</html>
```